We are a recruitment company based in Norwich/Cambridge England.
I have included our company logo which we want to remain the same.

What we are looking for is a new creative Business card which will really stand out!!

Contact Information for Business Card

Harriet Dunmore
email: Harriet@plavex.co.uk
Address: Brackwell House
Fenmoor Enterprise Park
Partridge Way
Norwich
QB9 3KX
Tel:01632 960418

```html
<!DOCTYPE html>
<html lang="en">
<head>
<meta charset="utf-8">
<title>Plavex Business Card</title>
<link rel="stylesheet" href="https://fonts.googleapis.com/css2?family=Roboto:wght@400;500;700&family=Roboto+Condensed:wght@400;700&display=swap">
<style>
  :root {
    --backdrop: #3a332e;
    --card: #1f2225;
    --green: #7bc832;
    --grey: #8f9296;
    --silver: #b4b6b9;
    --white: #f2f2f2;
    --rule: #6d7074;
  }
  * { margin: 0; padding: 0; box-sizing: border-box; }
  html, body { width: 1200px; height: 769px; overflow: hidden; }
  body {
    background: var(--backdrop);
    font-family: "Roboto", Arial, sans-serif;
    position: relative;
  }
  .card {
    position: absolute;
    top: 230px;
    width: 540px;
    height: 309px;
    background: var(--card);
    border-radius: 3px;
    box-shadow: 0 6px 18px rgba(0,0,0,.45);
  }
  .card-front { left: 40px; }
  .card-back { left: 620px; }

  /* front */
  .front-brand {
    position: absolute; left: 0; right: 0; top: 98px;
    display: flex; align-items: center; justify-content: center; gap: 12px;
  }
  .brand-dot { width: 44px; height: 44px; border-radius: 50%; }
  .front-brand .brand-dot { background: var(--silver); }
  .brand-name { font-weight: 500; font-size: 44px; letter-spacing: -0.5px; line-height: 1; }
  .front-brand .brand-name { color: var(--silver); }
  .brand-tagline {
    font-size: 8px; letter-spacing: 2px; color: var(--grey); text-transform: none;
  }
  .front-tagline { position: absolute; top: 150px; left: 0; right: 0; text-align: center; }
  .front-web {
    position: absolute; top: 212px; left: 0; right: 0; text-align: center;
    color: var(--grey); font-size: 12px; letter-spacing: 8px;
  }

  /* back */
  .person { position: absolute; left: 32px; top: 40px; }
  .person-name {
    font-family: "Roboto Condensed", Arial, sans-serif; font-weight: 700;
    font-size: 20px; color: var(--green); text-transform: uppercase; line-height: 1.05;
  }
  .person-title {
    font-family: "Roboto Condensed", Arial, sans-serif;
    font-size: 14px; color: var(--grey); text-transform: uppercase;
  }
  .contact-list { position: absolute; left: 32px; top: 100px; list-style: none; }
  .contact-list li {
    display: flex; align-items: center; gap: 8px;
    color: var(--white); font-size: 13px; line-height: 19px;
  }
  .contact-list svg { width: 12px; height: 12px; flex: none; }
  .contact-list .no-icon { padding-left: 20px; }
  .divider {
    position: absolute; left: 32px; right: 32px; top: 186px;
    height: 1px; background: var(--rule);
  }
  .back-brand {
    position: absolute; right: 34px; top: 44px; text-align: right;
  }
  .back-brand .brand-row { display: flex; align-items: center; gap: 8px; justify-content: flex-end; }
  .back-brand .brand-dot { width: 34px; height: 34px; background: var(--grey); }
  .back-brand .brand-name { color: var(--green); font-size: 34px; }
  .back-brand .brand-tagline { display: block; margin-top: 4px; font-size: 7px; }
  .address {
    position: absolute; right: 34px; bottom: 28px; text-align: right;
    color: var(--white); font-size: 13px; line-height: 19px; font-weight: 500;
  }
  .address .web { letter-spacing: 2px; }
</style>
</head>
<body>
  <section class="card card-front">
    <div class="front-brand">
      <span class="brand-dot"></span>
      <span class="brand-name">Plavex</span>
    </div>
    <div class="front-tagline brand-tagline">Technology Recruitment</div>
    <div class="front-web">www.plavex.co.uk</div>
  </section>

  <section class="card card-back">
    <div class="person">
      <div class="person-name">Harriet Dunmore</div>
      <div class="person-title">CEO/Founder</div>
    </div>

    <ul class="contact-list">
      <li>
        <svg viewBox="0 0 12 12" aria-hidden="true"><path d="M2.5 1h2l1 2.5-1.3 1a6 6 0 0 0 3.3 3.3l1-1.3L11 7.5v2A1.5 1.5 0 0 1 9.5 11 8.5 8.5 0 0 1 1 2.5 1.5 1.5 0 0 1 2.5 1z" fill="var(--green)"/></svg>
        01632 960418
      </li>
      <li>
        <svg viewBox="0 0 12 12" aria-hidden="true"><rect x="3" y="0.8" width="6" height="10.4" rx="1" fill="none" stroke="var(--green)" stroke-width="1.2"/><rect x="5" y="9" width="2" height="1" fill="var(--green)"/></svg>
        01632 960419
      </li>
      <li>
        <svg viewBox="0 0 12 12" aria-hidden="true"><rect x="1" y="3" width="10" height="7" rx="1" fill="var(--green)"/><rect x="3" y="1" width="6" height="3" fill="none" stroke="var(--green)" stroke-width="1"/></svg>
        01632 960420
      </li>
      <li>
        <svg viewBox="0 0 12 12" aria-hidden="true"><rect x="1" y="2" width="10" height="8" fill="var(--green)"/><path d="M3 6l2 2 4-4" fill="none" stroke="var(--card)" stroke-width="1.4"/></svg>
        Harriet@plavex.co.uk
      </li>
    </ul>

    <div class="divider"></div>

    <div class="back-brand">
      <div class="brand-row">
        <span class="brand-dot"></span>
        <span class="brand-name">Plavex</span>
      </div>
      <span class="brand-tagline">Technology Recruitment</span>
    </div>

    <address class="address" style="font-style:normal">
      Brackwell House, Partridge Way<br>
      Norwich QB9 3KX<br>
      <span class="web">www.plavex.co.uk</span>
    </address>
  </section>
</body>
</html>
```